Business Card Design for company

We want new business cards. We'd like something different-- yet still highly professional. Our tagline is Providing leadership, delivering success. Stock photos are ok, as long as they are relevant and look upscale.

Target Market(s)

Architecture/Business Management Consulting/Engineering Consulting

Contact Information for Business Card

dark gray background with pops of blue might be good, but you tell me. You're the designers. Rounded corners might be nice, but again, you tell me.

Font styles to use
Serif
Sans Serif

Colors
3276b5
5c5c5c
9d9d9d
fbfbfb

Requirements
Nice to have
• Something different, but still very professional.

```html
<!DOCTYPE html>
<html lang="en">
<head>
<meta charset="utf-8">
<title>Veltro Partners – Business Card</title>
<link href="https://fonts.googleapis.com/css2?family=Arimo:wght@400;700&display=swap" rel="stylesheet">
<style>
  :root {
    --brand-blue: #2b6299;
    --charcoal: #4b4d52;
    --text-gray: #5c5c5c;
    --paper: #ffffff;
    --backdrop: #e4e4e4;
  }
  * { margin: 0; padding: 0; box-sizing: border-box; }
  html, body {
    width: 1125px; height: 1200px; overflow: hidden;
    background: var(--backdrop);
    font-family: "Arimo", Arial, sans-serif;
  }
  .card {
    position: absolute; left: 150px; width: 825px; height: 472px;
  }
  .card-front { top: 98px; background: var(--paper); }
  .card-back { top: 631px; background: var(--charcoal); display: flex; align-items: center; justify-content: center; }

  .wordmark {
    position: absolute; left: 77px; top: 150px; width: 305px;
    color: var(--brand-blue); font-weight: 700; font-size: 50px;
    line-height: 1.05; letter-spacing: 2px; text-align: center;
  }
  .divider {
    position: absolute; left: 426px; top: 72px; width: 2px; height: 289px;
    background: linear-gradient(to bottom, rgba(92,92,92,0), #9d9d9d 20%, #9d9d9d 80%, rgba(92,92,92,0));
  }
  .contact { position: absolute; left: 464px; top: 76px; color: var(--text-gray); }
  .contact-name { color: var(--brand-blue); font-weight: 700; font-size: 30px; letter-spacing: .5px; line-height: 1; }
  .contact-title { font-weight: 700; font-size: 20px; margin-top: 3px; color: var(--text-gray); }
  .contact-address { font-size: 20px; line-height: 25px; margin-top: 16px; }
  .contact-list { list-style: none; margin-top: 13px; }
  .contact-list li { display: flex; align-items: center; font-size: 20px; height: 26.5px; }
  .contact-list svg { width: 18px; height: 18px; margin-right: 14px; fill: var(--brand-blue); flex: none; }

  .tagline-band {
    position: absolute; left: 0; top: 405px; width: 100%; height: 41px;
    background: var(--brand-blue); color: var(--paper);
    font-weight: 700; font-size: 20px;
    display: flex; align-items: center; justify-content: center; gap: 14px;
  }
  .tagline-dot { width: 7px; height: 7px; border-radius: 50%; background: var(--paper); }

  .back-wordmark {
    color: var(--brand-blue); font-weight: 700; font-size: 86px;
    line-height: 1.05; letter-spacing: 4px; text-align: center;
  }
</style>
</head>
<body>
  <section class="card card-front">
    <div class="wordmark">VELTRO<br>PARTNERS</div>
    <div class="divider"></div>
    <div class="contact">
      <div class="contact-name">DANIEL REYES</div>
      <div class="contact-title">CEO/FOUNDER</div>
      <div class="contact-address">4120 Cedar Hollow Road<br>Juneau, Alaska 34810</div>
      <ul class="contact-list">
        <li><svg viewBox="0 0 24 24"><path d="M6.6 10.8a15.1 15.1 0 0 0 6.6 6.6l2.2-2.2a1 1 0 0 1 1-.25 11.4 11.4 0 0 0 3.6.57 1 1 0 0 1 1 1V20a1 1 0 0 1-1 1A17 17 0 0 1 3 4a1 1 0 0 1 1-1h3.5a1 1 0 0 1 1 1c0 1.25.2 2.45.57 3.57a1 1 0 0 1-.25 1z"/></svg>615 302 7741</li>
        <li><svg viewBox="0 0 24 24"><path d="M7 1h10a2 2 0 0 1 2 2v18a2 2 0 0 1-2 2H7a2 2 0 0 1-2-2V3a2 2 0 0 1 2-2zm0 3v15h10V4z"/></svg>742 519 0863</li>
        <li><svg viewBox="0 0 24 24"><path d="M7 2h8l3 3v5H7zM4 11h16a2 2 0 0 1 2 2v7H2v-7a2 2 0 0 1 2-2zm3 4v2h10v-2z"/></svg>528 364 1197</li>
        <li><svg viewBox="0 0 24 24"><path d="M2 5h20v14H2zm2 2v.5l8 5.5 8-5.5V7l-8 5z"/></svg>daniel@veltropartners.com</li>
        <li><svg viewBox="0 0 24 24"><path d="M12 2a10 10 0 1 0 0 20 10 10 0 0 0 0-20zm-1 17.9A8 8 0 0 1 4.1 11H7l2 2v2l2 2zM17.9 16.4A2 2 0 0 0 16 15h-1v-3H9v-2h2V8h2V6.1a8 8 0 0 1 4.9 10.3z"/></svg>www.veltropartners.com</li>
      </ul>
    </div>
    <div class="tagline-band">
      <span>Providing leadership</span><span class="tagline-dot"></span><span>delivering success</span>
    </div>
  </section>

  <section class="card card-back">
    <div class="back-wordmark">VELTRO<br>PARTNERS</div>
  </section>
</body>
</html>
```